Bork Ventures, Inc. Website redesign

Revamp the website, it is old and outdated. www.borkventuresinc.example

Target Market(s)

Information Technology Consulting and Staffing

Coding

Coded - Design and coding required

Number of Pages Required

5+ page

Colors

Designer to choose colors to be used in the design.

Requirements
Must have
• Outlined text boxes just like from the Tolvane.example site. A clean look

```html
<!DOCTYPE html>
<html lang="en">
<head>
<meta charset="utf-8">
<title>Bork Ventures, Inc. – IT Consulting</title>
<link href="https://fonts.googleapis.com/css2?family=Maven+Pro:wght@400;500;600&family=Lato:wght@400;700&display=swap" rel="stylesheet">
<style>
:root{
  --brand:#a31c37;
  --brand-dark:#8a1630;
  --ink:#111111;
  --muted:#555555;
  --blush:#f4e7ea;
  --card-line:#e6e6e6;
  --white:#ffffff;
}
*{box-sizing:border-box;margin:0;padding:0}
html,body{width:1200px;height:2948px;overflow:hidden;background:var(--white)}
body{position:relative;font-family:'Lato',sans-serif;color:var(--ink)}
.abs{position:absolute}
.heading{font-family:'Maven Pro',sans-serif;font-weight:500;color:var(--ink)}
.btn{position:absolute;display:flex;align-items:center;justify-content:center;background:var(--brand);color:var(--white);font-family:'Maven Pro',sans-serif;font-size:16px;clip-path:polygon(14% 0,86% 0,100% 50%,86% 100%,14% 100%,0 50%)}

/* hero */
.hero{position:absolute;left:0;top:0;width:1200px;height:700px;overflow:hidden}
.hero-photo{position:absolute;inset:0;background:radial-gradient(ellipse at 55% 30%,#b9b9b9 0%,#8a8a8a 30%,#4a4a4a 65%,#2a2a2a 100%)}
.hero-wave{position:absolute;left:0;top:580px}
.brand-name{position:absolute;left:161px;top:26px;font-family:'Maven Pro',sans-serif;font-weight:600;font-size:30px;letter-spacing:3px;color:var(--brand)}
.nav{position:absolute;top:28px;right:164px;display:flex;gap:8px;font-size:12.5px;font-weight:700}
.nav a{color:var(--ink);text-decoration:none;padding:6px 12px;border:1px solid transparent}
.nav a.active{border-color:#333}
.hero-kicker{position:absolute;top:174px;width:1200px;text-align:center;font-family:'Maven Pro',sans-serif;font-size:26px;color:var(--ink)}
.hero-title{position:absolute;top:214px;width:1200px;text-align:center;font-family:'Maven Pro',sans-serif;font-weight:500;font-size:52px;color:var(--brand)}
.hero-text{position:absolute;top:286px;left:330px;width:540px;text-align:center;font-size:13.5px;line-height:21px;color:var(--white)}
.hero-arrow{position:absolute;top:317px}

/* welcome */
.welcome-title{left:162px;top:770px;font-size:38px}
.body-copy{font-size:11.5px;line-height:21px;color:var(--muted)}
.video{left:637px;top:769px;width:376px;height:300px;border-radius:4px;background:linear-gradient(160deg,#0c1b33 0%,#1f4e6e 45%,#0e2440 100%)}

/* services */
.svc-card{position:absolute;width:202px;height:150px;background:var(--white);box-shadow:0 0 10px rgba(0,0,0,.12);display:flex;flex-direction:column;align-items:center;justify-content:center;gap:14px;font-family:'Maven Pro',sans-serif;font-weight:500;font-size:13.5px}

/* strategy */
.strategy{position:absolute;left:0;top:1578px;width:1200px;height:436px;background:var(--blush)}
.step{position:absolute;top:244px;width:100px;text-align:center}
.step-ring{width:98px;height:98px;margin:0 auto;border-radius:50%;border:2px solid var(--brand);background:var(--white);display:flex;align-items:center;justify-content:center;box-shadow:inset 0 0 0 6px #f5dde2}
.step-label{margin-top:10px;font-family:'Maven Pro',sans-serif;font-weight:500;font-size:13.5px}

/* news */
.news-card{position:absolute;top:2155px;width:278px;height:315px;border:1px solid var(--card-line);padding:7px}
.news-photo{width:262px;height:165px}
.news-title{margin:12px 5px 0;font-family:'Maven Pro',sans-serif;font-weight:500;font-size:12.5px}
.news-date{margin:3px 5px 0;font-size:10px;color:var(--brand)}
.news-text{margin:6px 5px 0;font-size:11px;line-height:19.5px;color:var(--muted)}

/* contact */
.map{left:0;top:2638px;width:1200px;height:265px;background:linear-gradient(135deg,#eceef0,#e3e6e9 50%,#eceae3)}
.contact-box{left:191px;top:2658px;width:226px;height:185px;background:var(--white)}
.contact-head{height:38px;background:var(--brand);color:var(--white);font-family:'Maven Pro',sans-serif;font-size:16px;display:flex;align-items:center;justify-content:center}
.contact-row{display:flex;gap:14px;padding:0 16px;margin-top:14px;font-size:11.5px;line-height:18px;align-items:flex-start}
.footer{left:0;top:2903px;width:1200px;height:45px;background:var(--brand);color:var(--white);font-size:11.5px;display:flex;align-items:center;justify-content:center}
</style>
</head>
<body>

<header class="hero">
  <div class="hero-photo" role="img" aria-label="Photo of a person working at a desktop computer in an office"></div>
  <svg class="hero-wave" width="1200" height="120" viewBox="0 0 1200 120">
    <path d="M0 100 C120 120 220 112 330 96 C450 78 540 30 640 40 C720 48 800 100 880 92 C950 86 960 40 1030 30 C1100 22 1160 40 1200 60 L1200 120 L0 120 Z" fill="var(--white)"/>
    <path d="M0 100 C120 120 220 112 330 96 C450 78 540 30 640 40 C720 48 800 100 880 92 C950 86 960 40 1030 30 C1100 22 1160 40 1200 60" fill="none" stroke="var(--brand)" stroke-width="6"/>
  </svg>
  <div class="brand-name">BORK VENTURES</div>
  <nav class="nav">
    <a>Home</a><a class="active">About Us</a><a>Services</a><a>Strategy</a><a>IT News</a><a>Contact Us</a>
  </nav>
  <div class="hero-kicker">BORK VENTURES</div>
  <h1 class="hero-title">Mission Integrity Results</h1>
  <p class="hero-text">Bork Ventures, Inc. is an 8(a) full-service IT consulting company based in the Washington, DC Metro area. We offer specialized, highly customized technology solutions for our customers located throughout the United States.</p>
  <div class="btn" style="left:508px;top:382px;width:184px;height:52px;font-size:19px;font-weight:500">Contact Us</div>
  <svg class="hero-arrow" style="left:56px" width="54" height="54" viewBox="0 0 54 54"><circle cx="27" cy="27" r="25.5" fill="none" stroke="#fff" stroke-width="1.5"/><path d="M40 27H14M24 17L14 27L24 37" fill="none" stroke="#fff" stroke-width="2"/></svg>
  <svg class="hero-arrow" style="left:1090px" width="54" height="54" viewBox="0 0 54 54"><circle cx="27" cy="27" r="25.5" fill="none" stroke="#fff" stroke-width="1.5"/><path d="M14 27H40M30 17L40 27L30 37" fill="none" stroke="#fff" stroke-width="2"/></svg>
</header>

<section>
  <h2 class="heading abs welcome-title">Welcome To Bork Ventures</h2>
  <div class="abs body-copy" style="left:162px;top:829px;width:420px">
    <p>Bork Ventures, Inc. is an 8(a) innovative and rapidly growing full-service IT consulting firm. We provide our clients with cutting-edge technologies and the know-how to apply them to their individual business models.</p>
    <p>For over 20 + years, we have been providing reliable IT solutions to businesses in the Washington, DC Metro area and beyond. Our comprehensive services provide clients with unique technology solutions that are customized to meet the specific demands of their business.</p>
  </div>
  <div class="btn" style="left:160px;top:1023px;width:128px;height:38px">Read More</div>
  <div class="abs video" role="img" aria-label="Video still of server rack hardware with blue lights"></div>
  <svg class="abs" style="left:802px;top:896px" width="46" height="46" viewBox="0 0 46 46"><circle cx="23" cy="23" r="22" fill="var(--brand)" opacity=".9"/><path d="M19 15L30 23L19 31Z" fill="#fff"/></svg>
</section>

<section>
  <div class="svc-card" style="left:161px;top:1185px">
    <svg width="68" height="56" viewBox="0 0 68 56" fill="none" stroke="var(--brand)" stroke-width="2"><rect x="12" y="2" width="54" height="38"/><path d="M34 40v10M24 52h20"/><rect x="2" y="10" width="24" height="38" fill="#fff"/><rect x="34" y="20" width="14" height="26" fill="#fff"/></svg>
    <span>Hardware / Software Sales</span>
  </div>
  <div class="svc-card" style="left:386px;top:1162px">
    <svg width="62" height="62" viewBox="0 0 62 62" fill="none" stroke="var(--brand)" stroke-width="2"><circle cx="31" cy="29" r="14"/><circle cx="31" cy="29" r="21" stroke-dasharray="6 4"/><text x="31" y="35" text-anchor="middle" font-size="16" fill="var(--brand)" stroke="none" font-family="Lato">$</text><path d="M14 48l-8 10M48 48l8 10"/></svg>
    <span>Professional Services</span>
  </div>
  <div class="svc-card" style="left:161px;top:1357px">
    <svg width="64" height="62" viewBox="0 0 64 62" fill="none" stroke="var(--brand)" stroke-width="2"><circle cx="32" cy="10" r="6"/><circle cx="22" cy="26" r="6"/><circle cx="42" cy="26" r="6"/><circle cx="12" cy="44" r="6"/><circle cx="32" cy="44" r="6"/><circle cx="52" cy="44" r="6"/><path d="M4 2v10M60 2v10"/></svg>
    <span>Technology Assessment</span>
  </div>
  <div class="svc-card" style="left:386px;top:1334px">
    <svg width="62" height="62" viewBox="0 0 62 62" fill="none" stroke="var(--brand)" stroke-width="2"><rect x="24" y="2" width="36" height="28"/><path d="M32 24v-6M40 24v-10M48 24v-14"/><circle cx="12" cy="26" r="6"/><circle cx="12" cy="44" r="5"/><circle cx="30" cy="44" r="5"/><circle cx="48" cy="44" r="5"/><path d="M4 60c0-8 16-8 16 0M22 60c0-8 16-8 16 0M40 60c0-8 16-8 16 0"/></svg>
    <span>Technology Consulting</span>
  </div>
  <h2 class="heading abs" style="left:642px;top:1194px;font-size:38px">What We Provide?</h2>
  <p class="abs body-copy" style="left:642px;top:1253px;width:290px;font-size:11.5px;line-height:19.5px">Bork Ventures, Inc. organizes our Services into four key areas. While these four services can be implemented individually the majority of our projects successfully combine componets from each. Our people and our process is what makes us successful in providing these services.</p>
  <div class="btn" style="left:641px;top:1409px;width:128px;height:38px">Learn More</div>
</section>

<section class="strategy">
  <h2 class="heading" style="position:absolute;top:60px;width:1200px;text-align:center;font-size:38px">Our Strategy</h2>
  <p class="body-copy" style="position:absolute;left:340px;top:128px;width:520px;text-align:center;font-size:11.5px;line-height:19.5px">Civilian and Federal agencies are facing increased demands driven by the changing economic environment and shifts in the way products and services are sold and delivered. These factors have created an imperative to leverage new and innovative technology solution architectures like cloud computing to help reduce cost and deliver profit-driving IT capabilities faster than ever before.</p>
  <svg style="position:absolute;left:244px;top:248px" width="712" height="90" viewBox="0 0 712 90" fill="none" stroke="var(--brand)" stroke-width="1" opacity=".7">
    <path d="M40 25 C80 5 120 5 150 20"/><path d="M222 70 C260 90 300 90 330 72"/><path d="M400 25 C440 5 480 5 510 20"/><path d="M580 70 C620 90 660 90 690 72"/>
  </svg>
  <div class="step" style="left:194px"><div class="step-ring"><svg width="46" height="46" viewBox="0 0 46 46" fill="none" stroke="var(--brand)" stroke-width="2"><path d="M12 42V30C4 24 6 6 22 6s20 14 14 22v6h-6v8"/><circle cx="22" cy="18" r="5"/></svg></div><div class="step-label">Assess</div></div>
  <div class="step" style="left:372px"><div class="step-ring"><svg width="46" height="46" viewBox="0 0 46 46" fill="none" stroke="var(--brand)" stroke-width="2"><rect x="10" y="4" width="28" height="36"/><circle cx="20" cy="26" r="7"/><path d="M25 31l8 8M16 10h16M30 16h4"/></svg></div><div class="step-label">Recommend</div></div>
  <div class="step" style="left:550px"><div class="step-ring"><svg width="46" height="46" viewBox="0 0 46 46" fill="none" stroke="var(--brand)" stroke-width="2"><rect x="4" y="6" width="38" height="30"/><path d="M12 24v-6M18 24v-10M24 24v-4M30 24v-12"/><circle cx="14" cy="40" r="3"/><path d="M22 40h16"/></svg></div><div class="step-label">Implement</div></div>
  <div class="step" style="left:728px"><div class="step-ring"><svg width="46" height="46" viewBox="0 0 46 46" fill="none" stroke="var(--brand)" stroke-width="2"><rect x="4" y="6" width="38" height="26"/><path d="M10 26l8-8 6 5 10-10M16 40h14M23 32v8"/></svg></div><div class="step-label">Monitor</div></div>
  <div class="step" style="left:906px"><div class="step-ring"><svg width="46" height="46" viewBox="0 0 46 46" fill="none" stroke="var(--brand)" stroke-width="2"><circle cx="26" cy="18" r="13" stroke-dasharray="5 3"/><circle cx="18" cy="28" r="8"/><path d="M12 34l-8 8M22 22l10-10M28 12h4v4"/></svg></div><div class="step-label">Manage</div></div>
</section>

<section>
  <h2 class="heading abs" style="top:2078px;width:1200px;text-align:center;font-size:38px">Our News</h2>
  <article class="news-card" style="left:161px">
    <div class="news-photo" role="img" aria-label="Photo of network switch ports with connected cables" style="background:linear-gradient(135deg,#e9e9e6,#9a9a94 55%,#2a2a2a)"></div>
    <h3 class="news-title">Lorem Ipsum is simply dummy text of the.</h3>
    <p class="news-date">4 August 2019</p>
    <p class="news-text">Lorem Ipsum is simply dummy text of the printing and typesetting industry. Lorem Ipsum has been the industry's standard dummy text ever since the 1500s</p>
  </article>
  <article class="news-card" style="left:461px">
    <div class="news-photo" role="img" aria-label="Photo of colleagues working at laptops in an office" style="background:linear-gradient(135deg,#1d2f4f,#6c7f96 50%,#c9c4b4)"></div>
    <h3 class="news-title">Lorem Ipsum is simply dummy text of the.</h3>
    <p class="news-date">4 August 2019</p>
    <p class="news-text">Lorem Ipsum is simply dummy text of the printing and typesetting industry. Lorem Ipsum has been the industry's standard dummy text ever since the 1500s</p>
  </article>
  <article class="news-card" style="left:761px">
    <div class="news-photo" role="img" aria-label="Photo of a technician connecting cables in a server rack" style="background:linear-gradient(135deg,#2b3c4e,#7d95ad 50%,#d7dde2)"></div>
    <h3 class="news-title">Lorem Ipsum is simply dummy text of the.</h3>
    <p class="news-date">4 August 2019</p>
    <p class="news-text">Lorem Ipsum is simply dummy text of the printing and typesetting industry. Lorem Ipsum has been the industry's standard dummy text ever since the 1500s</p>
  </article>
  <div class="btn" style="left:536px;top:2530px;width:128px;height:38px">Learn More</div>
</section>

<section>
  <div class="abs map" role="img" aria-label="Street map showing the office location"></div>
  <div class="abs contact-box">
    <div class="contact-head">Contact Info</div>
    <div class="contact-row" style="margin-top:22px"><svg width="20" height="18" viewBox="0 0 20 18"><path d="M4 1l4 4-2 3c1 2 3 4 5 5l3-2 4 4-3 3C8 17 2 10 1 4z" fill="var(--brand)"/></svg><span>555-014-2287</span></div>
    <div class="contact-row"><svg width="20" height="16" viewBox="0 0 20 16" fill="none" stroke="var(--brand)" stroke-width="2"><rect x="1" y="2" width="18" height="12"/><path d="M1 2l9 7 9-7"/></svg><span>info@borkventuresinc.example</span></div>
    <div class="contact-row"><svg width="20" height="22" viewBox="0 0 20 22"><path d="M10 1a7 7 0 0 0-7 7c0 5 7 13 7 13s7-8 7-13a7 7 0 0 0-7-7z" fill="var(--brand)"/><circle cx="10" cy="8" r="2.5" fill="#fff"/></svg><span>4821 Harrow Lane<br>Fernbrook, MD 20990</span></div>
  </div>
  <svg class="abs" style="left:586px;top:2812px" width="24" height="32" viewBox="0 0 24 32"><path d="M12 1a11 11 0 0 0-11 11c0 8 11 19 11 19s11-11 11-19A11 11 0 0 0 12 1z" fill="var(--brand)"/><circle cx="12" cy="12" r="4" fill="var(--brand-dark)"/></svg>
  <footer class="abs footer">© 2019 Bork Ventures, All Rights Reserved. Terms &amp; Conditions | Privacy Policy.</footer>
</section>

</body>
</html>
```